Gooey Tides

I am creating an online slime shop that will sell handmade custom slimes. I need to be able to have payment/shipping options and the ability to change product photos since the product and product name will change often

Target Market(s)

Slime

Industry/Entity Type

Retail - online sales

Coding

Coded - Design and coding required

Number of Pages Required

2 page

Font styles to use
Sans Serif

Colors
0094D4
00A9DD
6FCCEA
C7EBF8
E9F6FB
E54698
E96AAD
F1A4CE
F9D9EA
FCEFF6
A7469A
B969AE
D3A5CF
EDDBEB
F8F0F9

Requirements
Must have
• My logo, my domain, ability to change photos of products for sale, payment options, shipping options, social media links, contact us,

```html
<!DOCTYPE html>
<html lang="en">
<head>
<meta charset="utf-8">
<title>Gooey Tides – Handmade Custom Slimes</title>
<link rel="stylesheet" href="https://fonts.googleapis.com/css2?family=Lato:wght@400;700;900&display=swap">
<style>
  :root {
    --teal: #9ddcdc;
    --purple: #9b30c7;
    --magenta: #c7408f;
    --grad-start: #c243a0;
    --grad-end: #8b2fd0;
    --ink: #111111;
    --text: #333333;
    --muted: #555555;
    --white: #ffffff;
    --black: #000000;
    --sky: #b9dbe6;
  }
  * { box-sizing: border-box; margin: 0; padding: 0; }
  html, body { width: 1200px; height: 3313px; overflow: hidden; }
  body {
    position: relative;
    background: var(--white);
    font-family: "Lato", Arial, sans-serif;
    color: var(--text);
  }
  .abs { position: absolute; }

  /* Navigation */
  .site-nav { position: absolute; top: 0; left: 0; width: 1200px; height: 85px; background: var(--white); }
  .nav-link { position: absolute; top: 32px; font-size: 16px; color: var(--ink); text-decoration: none; }
  .nav-link.is-active { color: var(--magenta); }
  .nav-link.is-active::after {
    content: ""; position: absolute; left: -2px; right: -2px; bottom: -7px;
    height: 3px; border-radius: 2px; background: var(--purple);
  }

  /* Hero */
  .hero-band { position: absolute; top: 85px; left: 0; width: 1200px; height: 727px; }
  .brand-badge {
    position: absolute; left: 433px; top: -126px; width: 334px; height: 334px;
    border-radius: 50%; background: var(--white);
    display: flex; align-items: flex-end; justify-content: center; padding-bottom: 62px;
  }
  .brand-name { font-weight: 900; font-size: 30px; color: var(--magenta); letter-spacing: 1px; }
  .hero-photo {
    position: absolute; left: 225px; top: 386px; width: 740px; height: 341px;
    border-radius: 40px;
    background: linear-gradient(180deg, #a98cc8 0%, #7a4d9e 55%, #d9b59c 100%);
  }
  .hero-title {
    position: absolute; top: 238px; left: 0; width: 1200px; text-align: center;
    font-weight: 700; font-size: 52px; line-height: 72px; color: #b03ab5;
  }
  .hero-title .light { color: var(--white); }
  .btn {
    position: absolute; height: 43px; border-radius: 22px;
    background: linear-gradient(90deg, var(--grad-start), var(--grad-end));
    color: var(--white); font-weight: 700; font-size: 16px;
    display: flex; align-items: center; justify-content: center; text-decoration: none;
  }
  .arrow-btn {
    position: absolute; width: 38px; height: 38px; border-radius: 50%;
    background: var(--black); display: flex; align-items: center; justify-content: center;
  }

  /* About */
  .section-title { position: absolute; font-weight: 700; font-size: 40px; color: var(--ink); }
  .section-title .accent { color: var(--magenta); }
  .about-copy { position: absolute; left: 661px; top: 925px; width: 425px; font-size: 15.5px; line-height: 25.7px; color: var(--text); }
  .about-copy p + p { margin-top: 25.7px; }

  /* Products */
  .featured-intro { position: absolute; left: 250px; top: 1454px; width: 700px; text-align: center; font-size: 15.5px; line-height: 23px; color: var(--muted); }
  .product-photo { position: absolute; border-radius: 50%; }
  .product-card { position: absolute; top: 1982px; width: 290px; text-align: center; }
  .product-name { font-weight: 700; font-size: 28px; color: var(--purple); }
  .product-text { margin-top: 10px; font-size: 15.5px; line-height: 23px; color: var(--muted); }

  /* Testimonials */
  .testimonials {
    position: absolute; left: 60px; top: 2249px; width: 1079px; height: 404px; border-radius: 202px;
    background: linear-gradient(180deg, #9a3bcc 0%, #b944ae 55%, #d84c94 100%);
    color: var(--white); text-align: center;
  }
  .testimonials h2 { margin-top: 80px; font-weight: 700; font-size: 40px; line-height: 48px; }
  .quote { width: 750px; margin: 14px auto 0; font-size: 19px; line-height: 24.5px; }
  .quote-mark { position: absolute; font-weight: 900; font-size: 64px; line-height: 1; }
  .reviewer { margin-top: 12px; font-size: 20px; }
  .dots { position: absolute; left: 498px; top: 310px; display: flex; gap: 8px; }
  .dots span { width: 22px; height: 8px; background: var(--white); border-radius: 1px; }

  /* Footer */
  .footer-band { position: absolute; top: 2743px; left: 0; width: 1200px; height: 570px; }
  .footer-brand { position: absolute; left: 107px; top: 2940px; width: 300px; text-align: center; font-weight: 900; font-size: 34px; color: var(--magenta); }
  .footer-tagline { position: absolute; left: 107px; top: 3092px; width: 300px; text-align: center; font-size: 16px; line-height: 26px; color: var(--white); }
  .pay-badges { position: absolute; left: 154px; top: 3163px; display: flex; gap: 8px; }
  .pay-badges span { width: 38px; height: 23px; background: var(--white); border-radius: 2px; }
  .footer-heading { position: absolute; top: 2918px; font-weight: 700; font-size: 21px; color: var(--white); }
  .footer-heading .accent { color: var(--magenta); }
  .footer-list { position: absolute; top: 2968px; list-style: none; font-size: 15.5px; line-height: 38.6px; color: var(--white); }
  .contact-item { position: absolute; left: 642px; display: flex; gap: 22px; font-size: 15.5px; line-height: 25.7px; color: var(--white); }
  .contact-item svg { flex: none; margin-top: 4px; }
  .social-row { position: absolute; left: 638px; top: 3158px; display: flex; gap: 9px; }
  .social-row span { width: 38px; height: 38px; border-radius: 4px; display: flex; align-items: center; justify-content: center; }
  .social-row span i { width: 20px; height: 20px; border: 2px solid var(--white); border-radius: 50%; }
  .social-row .is-active { background: var(--purple); }
  .footer-rule { position: absolute; left: 112px; top: 3263px; width: 976px; height: 1px; background: #333; }
  .copyright { position: absolute; top: 3282px; left: 0; width: 1200px; text-align: center; font-size: 14px; color: var(--white); }
</style>
</head>
<body>

  <!-- Hero -->
  <svg class="hero-band" viewBox="0 0 1200 727" aria-hidden="true">
    <path d="M0 0 H1200 V617 Q600 837 0 617 Z" fill="var(--teal)"/>
  </svg>
  <div class="hero-photo" role="img" aria-label="Photo of two hands stretching glittery purple slime"></div>

  <h1 class="hero-title">Explore Our Colorful Collection of<br><span class="light">Slime Delights!</span></h1>
  <a class="btn" href="#" style="left:521px;top:391px;width:158px">Shop Now</a>

  <div class="arrow-btn" style="left:58px;top:345px"><svg width="14" height="14" viewBox="0 0 14 14"><path d="M9 2 L4 7 L9 12" stroke="#fff" stroke-width="2.4" fill="none"/></svg></div>
  <div class="arrow-btn" style="left:1104px;top:345px"><svg width="14" height="14" viewBox="0 0 14 14"><path d="M5 2 L10 7 L5 12" stroke="#fff" stroke-width="2.4" fill="none"/></svg></div>

  <!-- Navigation -->
  <nav class="site-nav">
    <a class="nav-link is-active" href="#" style="left:116px">Home</a>
    <a class="nav-link" href="#" style="left:207px">Shop</a>
    <a class="nav-link" href="#" style="left:292px">About Us</a>
    <a class="nav-link" href="#" style="left:823px">Product</a>
    <a class="nav-link" href="#" style="left:927px">Blog</a>
    <a class="nav-link" href="#" style="left:1008px">Contact Us</a>
    <div class="brand-badge"><span class="brand-name">Gooey Tides</span></div>
  </nav>

  <!-- About -->
  <section>
    <div class="abs" style="left:184px;top:811px;width:102px;height:102px;border-radius:50%;background:linear-gradient(135deg,#d04a9a,#b3368c)"></div>
    <div class="abs" style="left:407px;top:811px;width:102px;height:102px;border-radius:50%;background:linear-gradient(135deg,#a22fbf,#7d2cd0)"></div>
    <div class="abs" role="img" aria-label="Photo of a child stretching orange slime" style="left:113px;top:848px;width:464px;height:464px;border-radius:50%;background:radial-gradient(circle at 50% 60%,#f0a25a 0%,#c9d8df 45%,var(--sky) 100%)"></div>

    <h2 class="section-title" style="left:661px;top:842px">About <span class="accent">Us</span></h2>
    <div class="about-copy">
      <p>Lorem ipsum dolor sit amet, consectetur adipiscing elit, sed do eiusmod tempor incididunt ut labore et dolore magna aliqua. Quis ipsum suspendisse ultrices gravida. Risus commodo viverra maecenas accumsan lacus vel facilisis.</p>
      <p>Sed ut perspiciatis unde omnis iste natus error sit voluptatem accusantium doloremque laudantium, totam rem aperiam, eaque ipsa quae ab illo inventore veritatis et quasi architecto beatae vitae dicta sunt explicabo. Nemo enim ipsam voluptatem quia voluptas sit aspernatur aut odit aut fugit, sed quia consequuntur magni dolores eos qui ratione voluptatem sequi nesciunt.</p>
    </div>
    <a class="btn" href="#" style="left:661px;top:1271px;width:158px">Read More</a>
  </section>

  <!-- Featured products -->
  <section>
    <h2 class="section-title" style="left:0;width:1200px;text-align:center;top:1389px">Featured <span class="accent">Products</span></h2>
    <p class="featured-intro">Lorem ipsum dolor sit amet, consectetur adipiscing elit, sed do eiusmod tempor incididunt ut labore et dolore magna aliqua. Quis ipsum suspendisse ultrices gravida. Risus commodo viverra maecenas accumsan lacus vel facilisis.</p>

    <div class="product-photo" role="img" aria-label="Photo of a jar of blue slime with toppings" style="left:112px;top:1580px;width:368px;height:368px;background:linear-gradient(160deg,#3a3a3a 0%,#9fb7c4 45%,#6fa6bd 100%)"></div>
    <div class="product-photo" role="img" aria-label="Photo of a jar of swirled slime with toppings" style="left:720px;top:1580px;width:368px;height:368px;background:linear-gradient(160deg,#e07a9a 0%,#e5566f 45%,#d9b479 100%)"></div>
    <div class="product-photo" role="img" aria-label="Photo of a jar of pink slime with a waffle topping" style="left:402px;top:1557px;width:394px;height:394px;border:4px solid #fff;background:linear-gradient(180deg,#f0b8b0 0%,#e8879f 50%,#d46bc0 100%)"></div>

    <div class="arrow-btn" style="left:50px;top:1747px"><svg width="14" height="14" viewBox="0 0 14 14"><path d="M9 2 L4 7 L9 12" stroke="#fff" stroke-width="2.4" fill="none"/></svg></div>
    <div class="arrow-btn" style="left:1110px;top:1747px"><svg width="14" height="14" viewBox="0 0 14 14"><path d="M5 2 L10 7 L5 12" stroke="#fff" stroke-width="2.4" fill="none"/></svg></div>

    <div class="product-card" style="left:153px"><h3 class="product-name">Slime 1</h3><p class="product-text">Lorem ipsum dolor sit amet, consectetur adipiscing elit, sed do eiusmod tempor incididunt ut labore et dolore aliqua.</p></div>
    <div class="product-card" style="left:454px"><h3 class="product-name">Slime 2</h3><p class="product-text">Lorem ipsum dolor sit amet, consectetur adipiscing elit, sed do eiusmod tempor incididunt ut labore et dolore aliqua.</p></div>
    <div class="product-card" style="left:756px"><h3 class="product-name">Slime 3</h3><p class="product-text">Lorem ipsum dolor sit amet, consectetur adipiscing elit, sed do eiusmod tempor incididunt ut labore et dolore aliqua.</p></div>

    <a class="btn" href="#" style="left:519px;top:2119px;width:158px">Shop Now</a>
  </section>

  <!-- Testimonials -->
  <section class="testimonials">
    <h2>Our Testimonials</h2>
    <span class="quote-mark" style="left:136px;top:122px">“</span>
    <p class="quote">Lorem ipsum dolor sit amet, consectetur adipiscing elit, sed do eiusmod tempor incididunt ut labore et dolore magna aliqua. Ut enim ad minim veniam, quis nostrud exercitation ullamco laboris nisi ut aliquip ex ea commodo consequat.</p>
    <span class="quote-mark" style="left:800px;top:212px">”</span>
    <p class="reviewer">Marla T.</p>
    <div class="dots"><span></span><span></span><span></span></div>
  </section>

  <!-- Footer -->
  <svg class="footer-band" viewBox="0 0 1200 570" aria-hidden="true">
    <path d="M0 112 Q600 -112 1200 112 V570 H0 Z" fill="var(--black)"/>
  </svg>

  <div class="footer-brand">Gooey Tides</div>
  <p class="footer-tagline">Unleash Your Creativity with<br>Custom Slimes!</p>
  <div class="pay-badges"><span></span><span></span><span></span><span></span><span></span></div>

  <h4 class="footer-heading" style="left:473px">Main <span class="accent">Links</span></h4>
  <ul class="footer-list" style="left:473px">
    <li>Home</li><li>Shop</li><li>About Us</li><li>Product</li><li>Blog</li><li>Contact Us</li>
  </ul>

  <h4 class="footer-heading" style="left:642px">Contact <span class="accent">Us</span></h4>
  <div class="contact-item" style="top:2968px">
    <svg width="17" height="20" viewBox="0 0 17 20"><path d="M8.5 19 C8.5 19 2 12 2 7.5 A6.5 6.5 0 0 1 15 7.5 C15 12 8.5 19 8.5 19 Z" fill="none" stroke="#fff" stroke-width="1.5"/><circle cx="8.5" cy="7.5" r="2.3" fill="none" stroke="#fff" stroke-width="1.5"/></svg>
    <span>123, Gooey Tides Lorem ipsum<br>dolor sit amet Na 123456.</span>
  </div>
  <div class="contact-item" style="top:3049px">
    <svg width="17" height="17" viewBox="0 0 17 17"><path d="M3 1.5 L6 1.5 L7.5 5 L5.5 6.5 C6.5 8.5 8.5 10.5 10.5 11.5 L12 9.5 L15.5 11 L15.5 14 C15.5 15 14.5 15.8 13.5 15.7 C7 15 2 10 1.3 3.5 C1.2 2.5 2 1.5 3 1.5 Z" fill="none" stroke="#fff" stroke-width="1.4"/></svg>
    <span>+ 1 555 014 2290</span>
  </div>
  <div class="contact-item" style="top:3102px">
    <svg width="18" height="14" viewBox="0 0 18 14"><rect x="1" y="1" width="16" height="12" rx="1.5" fill="none" stroke="#fff" stroke-width="1.4"/><path d="M1.5 2 L9 8 L16.5 2" fill="none" stroke="#fff" stroke-width="1.4"/></svg>
    <span>info@gooeytides.com</span>
  </div>
  <div class="social-row">
    <span class="is-active"><i></i></span><span><i></i></span><span><i></i></span><span><i></i></span>
  </div>

  <h4 class="footer-heading" style="left:955px">Other <span class="accent">Links</span></h4>
  <ul class="footer-list" style="left:955px">
    <li>Help</li><li>Support</li><li>FAQs</li><li>Cookies Policy</li><li>Terms &amp; Conditions</li><li>Privacy Policy</li>
  </ul>

  <div class="footer-rule"></div>
  <p class="copyright">Copyright © 2024 Gooey Tides. All rights reserved.</p>

</body>
</html>
```